Business Card Design needed for start up company Halvora

In need of a new business card designed for a start up company based in Sydney, Halvora is a new start up innovative Company, our mission it to make property accessible for everyday Australian and to become the leading Real Estate platform in Australia. We want it to be fresh and clean.

Industry/Entity Type

Financial

Contact Information for Business Card

Section for Name
Section for Title

HALVORA - The Strength of Pooling
Mobile:
Direct:

Font styles to use
Sans Serif

Colors
33a6d7
0692cd
0255a3
ffffff

Requirements
Must have
• Logo, all business card details

```html
<!DOCTYPE html>
<html lang="en">
<head>
<meta charset="UTF-8">
<title>Halvora Business Card</title>
<link href="https://fonts.googleapis.com/css2?family=Roboto:wght@400;500;900&display=swap" rel="stylesheet">
<style>
  :root {
    --navy: #20497f;
    --sky: #1e9ad6;
    --white: #ffffff;
    --ink: #2a2a2a;
    --backdrop: #6d7378;
  }
  * { margin: 0; padding: 0; box-sizing: border-box; }
  html, body { width: 1200px; height: 900px; overflow: hidden; }
  body {
    background: var(--backdrop);
    font-family: "Roboto", Arial, sans-serif;
    position: relative;
  }
  .card {
    position: absolute;
    left: 320px;
    width: 560px;
    height: 320px;
    border-radius: 18px;
    overflow: hidden;
    box-shadow: 0 10px 24px rgba(0,0,0,0.3);
  }
  .card-front { top: 100px; background: var(--white); }
  .card-back { top: 480px; background: var(--navy); }
  .card-shapes { position: absolute; inset: 0; }

  .brand { position: absolute; display: flex; align-items: center; }
  .brand-dot { border-radius: 50%; background: var(--sky); }
  .brand-name { font-weight: 900; letter-spacing: 0.5px; }

  .card-front .brand { left: 34px; top: 30px; gap: 10px; }
  .card-front .brand-dot { width: 44px; height: 44px; }
  .card-front .brand-name { font-size: 38px; color: var(--navy); }

  .card-back .brand { left: 50%; top: 50%; transform: translate(-50%, -50%); gap: 16px; }
  .card-back .brand-dot { width: 78px; height: 78px; }
  .card-back .brand-name { font-size: 68px; color: var(--white); }

  .contact-list { position: absolute; left: 34px; top: 132px; list-style: none; }
  .contact-item {
    display: flex; align-items: center; gap: 10px;
    font-size: 14px; color: var(--ink); margin-bottom: 9px;
  }
  .contact-icon {
    width: 20px; height: 20px; background: var(--navy);
    border-radius: 3px; display: flex; align-items: center; justify-content: center;
  }

  .holder {
    position: absolute; right: 30px; top: 54px; text-align: right; color: var(--white);
    white-space: nowrap;
  }
  .holder-name { font-size: 18px; font-weight: 500; letter-spacing: 1px; }
  .holder-title { font-size: 11px; letter-spacing: 1.5px; margin-top: 4px; }

  .address {
    position: absolute; right: 34px; bottom: 30px; text-align: right;
    color: var(--white); font-size: 14px; line-height: 1.5; font-style: normal;
  }
</style>
</head>
<body>

<section class="card card-front">
  <svg class="card-shapes" width="560" height="320" viewBox="0 0 560 320">
    <polygon points="200,320 430,0 560,0 560,320" fill="var(--navy)"/>
    <polygon points="300,118 340,36 560,36 560,118" fill="var(--sky)"/>
  </svg>

  <div class="brand">
    <span class="brand-dot"></span>
    <span class="brand-name">HALVORA</span>
  </div>

  <ul class="contact-list">
    <li class="contact-item">
      <span class="contact-icon">
        <svg width="12" height="12" viewBox="0 0 24 24"><path fill="#fff" d="M6.6 10.8a15 15 0 0 0 6.6 6.6l2.2-2.2c.3-.3.7-.4 1-.2 1.1.4 2.3.6 3.6.6.6 0 1 .4 1 1V20c0 .6-.4 1-1 1A17 17 0 0 1 3 4c0-.6.4-1 1-1h3.5c.6 0 1 .4 1 1 0 1.3.2 2.5.6 3.6.1.3 0 .7-.2 1z"/></svg>
      </span>02-5550-1870
    </li>
    <li class="contact-item">
      <span class="contact-icon">
        <svg width="12" height="12" viewBox="0 0 24 24"><rect x="6" y="2" width="12" height="20" rx="2" fill="none" stroke="#fff" stroke-width="2.4"/><circle cx="12" cy="18" r="1.3" fill="#fff"/></svg>
      </span>0412-555-096
    </li>
    <li class="contact-item">
      <span class="contact-icon">
        <svg width="12" height="12" viewBox="0 0 24 24"><rect x="2" y="5" width="20" height="14" fill="none" stroke="#fff" stroke-width="2.4"/><path d="M2 5l10 8 10-8" fill="none" stroke="#fff" stroke-width="2.4"/></svg>
      </span>hello@halvora.com.au
    </li>
    <li class="contact-item">
      <span class="contact-icon">
        <svg width="12" height="12" viewBox="0 0 24 24"><circle cx="12" cy="12" r="9" fill="none" stroke="#fff" stroke-width="2.2"/><path d="M3 12h18M12 3c3 3 3 15 0 18M12 3c-3 3-3 15 0 18" fill="none" stroke="#fff" stroke-width="1.8"/></svg>
      </span>www.halvora.com.au
    </li>
  </ul>

  <div class="holder">
    <p class="holder-name">MARA LINDQVIST</p>
    <p class="holder-title">OWNER</p>
  </div>

  <address class="address">
    48 Harbour Lane, Suite 210<br>
    Sydney, NSW 2000
  </address>
</section>

<section class="card card-back">
  <div class="brand">
    <span class="brand-dot"></span>
    <span class="brand-name">HALVORA</span>
  </div>
</section>

</body>
</html>
```